Web Developer Needs a Business Card Design

I need a personal business card design that represents me as a web developer for potential employers. I would like the background to be a dark color on the front for contrast with my logo and name. The back will have all my information along with a smaller version of the logo. I want something with a modern look and feel, not too conservative. This will be used for potential employers and freelance work.

Industry/Entity Type

Business

Contact Information for Business Card

Front should have my logo and name. The back should have all my personal information which would include: name: Tom Varulek, phone: 570-614-3098, email: tomvarulek@quillbox.net, website url: www.tomvarulek.net, logo, web developer.

Font styles to use
Sans Serif

Requirements
Must have
• Must include my logo. The color palette base color will be the logo color.

```html
<!DOCTYPE html>
<html lang="en">
<head>
<meta charset="UTF-8">
<title>Tom Varulek — Business Card</title>
<link rel="stylesheet" href="https://fonts.googleapis.com/css2?family=Source+Sans+3:wght@400;600&display=swap">
<style>
  :root {
    --canvas: #e6e4e2;
    --card: #050505;
    --accent: #6ccab6;
    --ink-light: #ffffff;
  }
  * { box-sizing: border-box; margin: 0; padding: 0; }
  html, body {
    width: 1200px; height: 780px; overflow: hidden;
    background: var(--canvas);
    font-family: "Source Sans 3", "Myriad Pro", sans-serif;
  }
  .stage {
    position: relative; width: 1200px; height: 780px;
    display: flex; align-items: center; justify-content: center; gap: 60px;
  }
  .card {
    position: relative; width: 520px; height: 298px;
    background: var(--card); overflow: hidden;
    box-shadow: 0 10px 28px rgba(0,0,0,.28);
  }
  .card__band {
    position: absolute; left: 0; right: 0; bottom: 22px; height: 14px;
    background: var(--accent);
  }
  .brandmark {
    position: absolute; display: flex; align-items: center; gap: 10px;
    color: var(--accent); font-weight: 600;
  }
  .brandmark__dot {
    border: 5px solid var(--accent); border-radius: 50%;
  }
  /* front */
  .card--front .brandmark { left: 50%; top: 52px; transform: translateX(-50%); font-size: 30px; }
  .card--front .brandmark__dot { width: 96px; height: 96px; }
  .card--front .card__name {
    position: absolute; left: 140px; top: 176px;
    color: var(--accent); font-size: 32px; font-weight: 400;
  }
  /* back */
  .card--back .brandmark { left: 34px; top: 70px; flex-direction: column; gap: 6px; font-size: 20px; }
  .card--back .brandmark__dot { width: 104px; height: 104px; }
  .details {
    position: absolute; right: 26px; top: 48px; text-align: right;
  }
  .details__name { color: var(--accent); font-size: 32px; font-weight: 400; line-height: 1; }
  .details__role { color: var(--ink-light); font-size: 18px; margin-top: 2px; }
  .contact { list-style: none; margin-top: 14px; }
  .contact li {
    color: var(--ink-light); font-size: 16px; line-height: 22px;
    display: flex; justify-content: flex-end; align-items: center; gap: 10px;
  }
  .contact svg { width: 13px; height: 13px; flex: none; }
</style>
</head>
<body>
<main class="stage">
  <section class="card card--front" aria-label="Card front">
    <div class="brandmark"><span class="brandmark__dot"></span>Varulek</div>
    <p class="card__name">Tom Varulek</p>
    <div class="card__band"></div>
  </section>

  <section class="card card--back" aria-label="Card back">
    <div class="brandmark"><span class="brandmark__dot"></span>Varulek</div>
    <div class="details">
      <h1 class="details__name">Tom Varulek</h1>
      <p class="details__role">web developer</p>
      <ul class="contact">
        <li>570-614-3098
          <svg viewBox="0 0 13 13"><rect width="13" height="13" fill="#fff"/><path d="M4 3c1 0 1.4 1.6.8 2.2.6 1.4 1.4 2.2 2.8 2.8.6-.6 2.2-.2 2.2.8-1 1.4-3.4 1-5-1S2.6 4 4 3z" fill="#000"/></svg>
        </li>
        <li>www.tomvarulek.net
          <svg viewBox="0 0 13 13"><rect width="13" height="13" fill="#fff"/><circle cx="6.5" cy="6.5" r="4" fill="none" stroke="#000" stroke-width="1.2"/><path d="M2.5 6.5h8M6.5 2.5c-2 2.5-2 5.5 0 8M6.5 2.5c2 2.5 2 5.5 0 8" fill="none" stroke="#000" stroke-width=".9"/></svg>
        </li>
        <li>tomvarulek@quillbox.net
          <svg viewBox="0 0 13 13"><rect width="13" height="13" fill="#fff"/><rect x="2.5" y="4" width="8" height="5.5" fill="none" stroke="#000" stroke-width="1.1"/><path d="M2.5 4l4 3 4-3" fill="none" stroke="#000" stroke-width="1.1"/></svg>
        </li>
      </ul>
    </div>
    <div class="card__band"></div>
  </section>
</main>
</body>
</html>
```